QP Fiduciary Website Redesign Contest

We want to refresh our website to be more insitutional, professional for an international audience. We have designed a new logo for this purpose and that has been attached. A full brand brief and positioning statement has also been attached. Please read through all the documents carefully before designing. The old website is found here: https://qp-fiduciary.example/

Target Market(s)

Actuaries and associated businesses internationally

Industry/Entity Type

professional services - actuaries

Number of Pages Required

3 page

Font styles to use
Sans Serif

Colors
0054AA
0677BA
7BADD7
CADEEF
E8F1F8
0094D4
00A9DD
6FCCEA
C7EBF8
E9F6FB
F0912C
F2A743
F7CA91
FBE8D2
FDF5EE
EE7325
F08F49
F5BC92
FAE3D3
FDF4ED
EB3D1F
EC4F4E
F09395
F8D3D4
FCEDEE

Requirements
Must have
• blues and greens to match the logo color, complimentary colors, navigation
Nice to have
• old site: https://qp-fiduciary.example/

```html
<!DOCTYPE html>
<html lang="en">
<head>
<meta charset="utf-8">
<title>QP Fiduciary — Actuarial Software</title>
<link href="https://fonts.googleapis.com/css2?family=Inter:wght@400;500;600;700&family=Plus+Jakarta+Sans:wght@300;400;700;800&display=swap" rel="stylesheet">
<style>
:root{
  --navy:#04213a;
  --navy-deep:#021629;
  --blue:#0054AA;
  --blue-mid:#0677BA;
  --sky:#0094D4;
  --sky-light:#6FCCEA;
  --pale:#F1F6FA;
  --orange:#EE7325;
  --orange-light:#F0912C;
  --teal:#17B4A0;
  --purple:#6B3FA0;
  --ink:#1d2430;
  --muted:#55606e;
  --white:#ffffff;
}
*{margin:0;padding:0;box-sizing:border-box}
html,body{width:1200px;height:4570px;overflow:hidden}
body{font-family:"Inter",sans-serif;color:var(--ink);background:var(--white);position:relative}
.page{position:relative;width:1200px;height:4570px;overflow:hidden}
.abs{position:absolute}
.wordmark{font-family:"Plus Jakarta Sans",sans-serif;font-weight:400;letter-spacing:3px;color:var(--white);display:flex;align-items:center;gap:10px}
.btn{display:inline-flex;align-items:center;gap:12px;background:var(--orange);color:var(--white);font-weight:600;font-size:14px;border-radius:24px;padding:0 8px 0 24px;height:42px;text-decoration:none}
.btn .arrow{width:28px;height:28px;border-radius:50%;background:var(--white);display:flex;align-items:center;justify-content:center}
.section-title{font-family:"Plus Jakarta Sans",sans-serif;font-weight:300;font-size:35px;text-align:center;color:var(--ink);width:1200px;left:0;letter-spacing:.5px}
.section-title b{font-weight:800;color:var(--blue)}
.title-rule{width:44px;height:2px;background:var(--orange);left:578px}
.lead{width:1200px;left:0;text-align:center;font-size:14px;color:var(--ink);line-height:22px}
.hero{left:0;top:0;width:1200px;height:600px;background:radial-gradient(ellipse 420px 260px at 560px 330px,#0d5a8a 0%,rgba(6,50,85,.6) 45%,rgba(2,22,41,0) 80%),linear-gradient(180deg,#031a2e 0%,#06304f 70%,#0a3f66 100%)}
.nav{left:70px;top:14px;width:1060px;height:42px;display:flex;align-items:center}
.nav ul{display:flex;gap:34px;list-style:none;margin-left:80px;font-size:13px;color:var(--white)}
.nav li:first-child{color:var(--sky-light)}
.nav .btn{margin-left:auto;padding:0 20px;height:40px;font-size:13px}
.hero h1{left:0;width:1200px;top:166px;text-align:center;font-family:"Plus Jakarta Sans",sans-serif;font-weight:300;font-size:42px;line-height:52px;color:var(--white)}
.hero h1 b{font-weight:800}
.hero p{left:0;width:1200px;top:280px;text-align:center;color:var(--white);font-size:14px;line-height:23px}
.dlabel{font-size:12px;color:var(--muted);line-height:19px}
.dlabel strong{display:block;font-size:15px;font-weight:500;margin-bottom:6px;line-height:20px}
.path-visual{border-radius:16px;background:linear-gradient(30deg,#e6f6f3 0%,#eaf1f9 50%,#fdf1e6 100%)}
.sol-card{background:var(--white);border-radius:6px;box-shadow:0 4px 18px rgba(0,40,80,.08);width:286px;height:236px;text-align:center}
.sol-card h3{font-size:16px;font-weight:600;margin-top:70px}
.sol-card .rule{width:30px;height:1px;background:var(--orange);margin:14px auto 16px}
.sol-card p{font-size:12.5px;line-height:19px;color:var(--muted);padding:0 40px;height:66px}
.sol-card a{font-size:13px;text-decoration:none;font-weight:500}
.icon-disc{width:86px;height:86px;border-radius:50%;display:flex;align-items:center;justify-content:center;box-shadow:0 0 0 6px rgba(255,255,255,.8)}
.feat{width:260px;font-size:12.5px;line-height:19px;color:var(--muted)}
.feat strong{display:block;color:var(--ink);font-weight:600;font-size:15px;margin-bottom:4px}
.feat.right{text-align:right}
.insight{background:var(--white);width:286px;height:366px;border-radius:6px;box-shadow:0 4px 18px rgba(0,40,80,.08);overflow:hidden}
.insight .photo{height:188px;position:relative}
.insight .date{position:absolute;right:8px;top:8px;width:34px;height:40px;background:var(--sky);color:var(--white);text-align:center;font-weight:700;font-size:15px;line-height:20px;border-radius:2px}
.insight .date small{display:block;font-size:7px;line-height:8px}
.insight h4{font-size:15px;font-weight:600;line-height:20px;margin:20px 18px 10px}
.insight p{font-size:12px;line-height:19px;color:var(--muted);margin:0 18px 12px}
.insight a{color:var(--orange);font-size:12.5px;margin-left:18px;text-decoration:none}
.footer-links{display:flex;gap:38px;font-size:13px;color:var(--white);list-style:none}
</style>
</head>
<body>
<div class="page">

<section class="hero abs">
  <nav class="nav abs">
    <div class="wordmark" style="font-size:26px;">QP FIDUCIARY</div>
    <ul><li>Home</li><li>Platform</li><li>Solutions</li><li>Insights</li><li>Company</li><li>Contact</li></ul>
    <a class="btn" href="#">Request a Technical Walkthrough</a>
  </nav>
  <h1 class="abs">Actuarial Software For <b>Structured,</b><br><b>Auditable Financial Analysis.</b></h1>
  <p class="abs">Software that translates actuarial methodologies into disciplined decision-ready<br>analytical tools across diverse regulatory environments.</p>
  <a class="btn abs" href="#" style="left:448px;top:346px;">Request A Technical Walkthrough<span class="arrow"><svg width="14" height="14" viewBox="0 0 14 14"><path d="M2 7h9M7 3l4 4-4 4" stroke="#EE7325" stroke-width="2" fill="none"/></svg></span></a>
</section>
<svg class="abs" style="left:0;top:500px" width="1200" height="110" viewBox="0 0 1200 110">
  <path d="M0 70 C200 10 360 40 520 60 C700 85 820 10 1000 30 C1100 40 1160 20 1200 20 L1200 110 L0 110Z" fill="#6FCCEA"/>
  <path d="M0 90 C220 40 380 80 560 85 C760 90 880 40 1040 60 C1120 70 1170 60 1200 50 L1200 110 L0 110Z" fill="#ffffff"/>
</svg>

<h2 class="section-title abs" style="top:678px;">PLATFORM <b>OVERVIEW</b></h2>
<div class="title-rule abs" style="top:732px;"></div>
<p class="lead abs" style="top:752px;"><b style="font-weight:600">QP Fiduciary</b> develops modular actuarial software designed to support reserving, valuation, pricing,<br>and risk analysis workflows across diverse regulatory environments.</p>

<div class="path-visual abs" role="img" aria-label="Illustration of a rising growth path with four milestone icons ending in an upward arrow" style="left:340px;top:972px;width:530px;height:254px;"></div>
<div class="dlabel abs" style="left:380px;top:908px;width:226px;text-align:right;"><strong style="color:#F0912C">Built-in Auditability</strong>every change, input, and output<br>is tracked and reviewable</div>
<div class="dlabel abs" style="left:130px;top:1012px;width:200px;text-align:right;"><strong style="color:#17B4A0">Structured Workflows</strong>that guide users through every<br>step of the analysis process</div>
<div class="dlabel abs" style="left:876px;top:1034px;width:200px;"><strong style="color:#0677BA">Robust Governance<br>Features</strong>to ensure compliance across<br>teams and jurisdictions</div>
<div class="dlabel abs" style="left:595px;top:1234px;width:200px;"><strong style="color:#6B3FA0">Full Transparency Of<br>Assumptions</strong>with version control and<br>documentation</div>
<a class="btn abs" href="#" style="left:508px;top:1350px;">Explore Platform<span class="arrow"><svg width="14" height="14" viewBox="0 0 14 14"><path d="M2 7h9M7 3l4 4-4 4" stroke="#EE7325" stroke-width="2" fill="none"/></svg></span></a>

<svg class="abs" style="left:0;top:1490px" width="1200" height="650" viewBox="0 0 1200 650" preserveAspectRatio="none">
  <path d="M0 20 C200 0 400 30 600 18 C800 6 1000 30 1200 14 L1200 620 C1000 640 800 610 600 622 C400 634 200 610 0 626Z" fill="#F1F6FA"/>
</svg>
<h2 class="section-title abs" style="top:1597px;">CORE <b>SOLUTIONS</b></h2>
<div class="title-rule abs" style="top:1650px;"></div>
<p class="lead abs" style="top:1669px;">Precision-built modules for the most demanding actuarial tasks</p>

<div class="sol-card abs" style="left:142px;top:1768px;"><h3>Reserving &amp; Valuation</h3><div class="rule"></div><p>Software supporting structured reserving workflows and financial reporting across jurisdictions.</p><a href="#" style="color:#0677BA">Learn More →</a></div>
<div class="sol-card abs" style="left:457px;top:1768px;"><h3>Pricing</h3><div class="rule"></div><p>Models supporting insurance and reinsurance pricing based on actuarial methodologies.</p><a href="#" style="color:#EE7325">Learn More →</a></div>
<div class="sol-card abs" style="left:772px;top:1768px;"><h3>Enterprise Risk Management</h3><div class="rule"></div><p>Software supporting reinsurance optimization and capital modeling.</p><a href="#" style="color:#17B4A0">Learn More →</a></div>

<div class="icon-disc abs" style="left:242px;top:1726px;background:#0677BA;"><svg width="44" height="44" viewBox="0 0 44 44" fill="none" stroke="#fff" stroke-width="2"><path d="M6 30c6-4 10-4 16 0h10M6 36h26l8-8"/><circle cx="26" cy="14" r="8"/><path d="M26 10v4l3 2"/></svg></div>
<div class="icon-disc abs" style="left:557px;top:1726px;background:#F0912C;"><svg width="44" height="44" viewBox="0 0 44 44" fill="none" stroke="#fff" stroke-width="2"><path d="M10 6h18l6 6v26H10z"/><circle cx="28" cy="30" r="8"/><path d="M28 25v10M15 14h10M15 20h8"/></svg></div>
<div class="icon-disc abs" style="left:872px;top:1726px;background:#17B4A0;"><svg width="44" height="44" viewBox="0 0 44 44" fill="none" stroke="#fff" stroke-width="2"><circle cx="22" cy="16" r="9"/><circle cx="22" cy="16" r="3"/><path d="M6 34c6-5 12-5 18-1h8l6-5"/></svg></div>

<h2 class="section-title abs" style="top:2213px;">PLATFORM <b>CHARACTERISTICS</b></h2>
<div class="title-rule abs" style="top:2268px;"></div>
<p class="lead abs" style="top:2292px;">Engineered for clarity, built to scale across borders</p>
<svg class="abs" style="left:420px;top:2350px" width="360" height="360" viewBox="0 0 360 360">
  <circle cx="180" cy="179" r="172" fill="none" stroke="#7BADD7" stroke-width="2"/>
</svg>
<div class="wordmark abs" style="left:458px;top:2509px;font-size:30px;color:#1d2430;">QP FIDUCIARY</div>
<div class="icon-disc abs" style="left:444px;top:2373px;width:78px;height:78px;background:#0054AA;"><svg width="38" height="38" viewBox="0 0 38 38" fill="none" stroke="#fff" stroke-width="2"><rect x="14" y="4" width="10" height="8"/><path d="M19 12v8M7 20h24M7 20v6M19 20v6M31 20v6"/><rect x="3" y="26" width="8" height="7"/><rect x="15" y="26" width="8" height="7"/><rect x="27" y="26" width="8" height="7"/></svg></div>
<div class="icon-disc abs" style="left:678px;top:2373px;width:78px;height:78px;background:#F0912C;"><svg width="38" height="38" viewBox="0 0 38 38" fill="none" stroke="#fff" stroke-width="2"><circle cx="22" cy="15" r="6"/><path d="M12 33c1-7 5-10 10-10s9 3 10 10"/><rect x="3" y="4" width="12" height="9" rx="2"/></svg></div>
<div class="icon-disc abs" style="left:444px;top:2606px;width:78px;height:78px;background:#6B3FA0;"><svg width="38" height="38" viewBox="0 0 38 38" fill="none" stroke="#fff" stroke-width="2"><path d="M8 4h16l6 6v24H8z"/><ellipse cx="19" cy="21" rx="8" ry="5"/><circle cx="19" cy="21" r="2"/></svg></div>
<div class="icon-disc abs" style="left:678px;top:2606px;width:78px;height:78px;background:#17B4A0;"><svg width="38" height="38" viewBox="0 0 38 38" fill="none" stroke="#fff" stroke-width="2"><circle cx="17" cy="17" r="12"/><path d="M25 25l9 9M11 22l4-5 4 3 5-7"/></svg></div>

<div class="feat right abs" style="left:160px;top:2382px;"><strong>Structured Workflows</strong>Consistent, repeatable processes from data to disclosure.</div>
<div class="feat abs" style="left:781px;top:2382px;"><strong>Multi-jurisdictional Review Support</strong>Localise assumptions, outputs, and reports for any regulator.</div>
<div class="feat right abs" style="left:160px;top:2615px;"><strong>Transparent Assumptions</strong>Every assumption exposed, documented, and linked to source.</div>
<div class="feat abs" style="left:781px;top:2615px;"><strong>Comparative Analysis Capability</strong>Run scenarios side by side — instantly see impacts.</div>
<a class="btn abs" href="#" style="left:448px;top:2748px;">Request A Technical Walkthrough<span class="arrow"><svg width="14" height="14" viewBox="0 0 14 14"><path d="M2 7h9M7 3l4 4-4 4" stroke="#EE7325" stroke-width="2" fill="none"/></svg></span></a>

<svg class="abs" style="left:0;top:2880px" width="1200" height="760" viewBox="0 0 1200 760" preserveAspectRatio="none">
  <path d="M0 20 C200 0 400 30 600 18 C800 6 1000 30 1200 14 L1200 740 C1000 756 800 728 600 740 C400 752 200 728 0 744Z" fill="#F1F6FA"/>
</svg>
<h2 class="section-title abs" style="top:2996px;">LATEST <b>INSIGHTS</b></h2>
<div class="title-rule abs" style="top:3050px;"></div>

<article class="insight abs" style="left:142px;top:3080px;">
  <div class="photo" role="img" aria-label="Photo of an analyst reviewing financial charts at a laptop" style="background:linear-gradient(135deg,#cfdde9,#7fa7c6 60%,#e4ecf2)"><div class="date">14<small>MAR</small></div></div>
  <h4>Advancing Actuarial Methods in a Changing Regulatory Landscape</h4>
  <p>Exploring how modern tools support evolving best practices in reserving and capital modeling.</p>
  <a href="#">Learn More →</a>
</article>
<article class="insight abs" style="left:457px;top:3080px;">
  <div class="photo" role="img" aria-label="Photo of colleagues reviewing printed reports on a desk" style="background:linear-gradient(135deg,#e58a3c,#f2b27a 55%,#d9d3cb)"><div class="date">14<small>MAR</small></div></div>
  <h4>Governance and Documentation in Actuarial Modeling</h4>
  <p>Why audit trails and assumption transparency are critical for internal and external review.</p>
  <a href="#">Learn More →</a>
</article>
<article class="insight abs" style="left:772px;top:3080px;">
  <div class="photo" role="img" aria-label="Photo of a professional at a trading desk with screens" style="background:linear-gradient(135deg,#3c4a52,#6f8a86 55%,#a9c2b8)"><div class="date">14<small>MAR</small></div></div>
  <h4>Multi-Jurisdictional Actuarial Practice: Challenges &amp; Solutions</h4>
  <p>Strategies for managing compliance across Solvency II, ICRB, and emerging frameworks.</p>
  <a href="#">Learn More →</a>
</article>
<a class="btn abs" href="#" style="left:515px;top:3483px;">Read Insights<span class="arrow"><svg width="14" height="14" viewBox="0 0 14 14"><path d="M2 7h9M7 3l4 4-4 4" stroke="#EE7325" stroke-width="2" fill="none"/></svg></span></a>

<section class="abs" style="left:142px;top:3742px;width:916px;height:376px;border-radius:18px;overflow:hidden;background:linear-gradient(120deg,#0054AA,#0677BA 45%,#0094D4);">
  <div class="abs" role="img" aria-label="Photo of hands holding a tablet with a glowing global network" style="left:520px;top:0;width:396px;height:376px;background:radial-gradient(circle at 150px 90px,#6fcfe6 0%,#1b6a8f 30%,#0a2740 70%,#061a2c 100%);"></div>
  <svg class="abs" style="left:430px;top:0" width="140" height="376" viewBox="0 0 140 376"><path d="M0 0 H90 C40 120 40 260 100 376 H0Z" fill="#0a6fb5"/><path d="M90 0 C40 120 40 260 100 376" stroke="#fff" stroke-width="6" fill="none"/></svg>
  <h2 class="abs" style="left:44px;top:78px;font-family:'Plus Jakarta Sans',sans-serif;font-weight:300;font-size:34px;line-height:42px;color:#fff;">READY TO SEE THE<br><b style="font-weight:800">PLATFORM IN ACTION?</b></h2>
  <p class="abs" style="left:44px;top:175px;width:410px;font-size:14px;line-height:23px;color:#fff;">Schedule a technical walkthrough and discover how QP Fiduciary can bring structure, transparency, and auditability to your actuarial processes.</p>
  <a class="btn abs" href="#" style="left:42px;top:271px;">Request A Technical Walkthrough<span class="arrow"><svg width="14" height="14" viewBox="0 0 14 14"><path d="M2 7h9M7 3l4 4-4 4" stroke="#EE7325" stroke-width="2" fill="none"/></svg></span></a>
</section>

<svg class="abs" style="left:0;top:4195px" width="1200" height="375" viewBox="0 0 1200 375" preserveAspectRatio="none">
  <path d="M0 20 C150 -5 300 50 480 50 C700 50 900 10 1200 30 L1200 375 L0 375Z" fill="#6FCCEA"/>
  <path d="M0 45 C200 30 350 80 560 65 C800 45 950 30 1200 50 L1200 375 L0 375Z" fill="#021a30"/>
</svg>
<div class="wordmark abs" style="left:438px;top:4364px;font-size:34px;">QP FIDUCIARY</div>
<ul class="footer-links abs" style="left:396px;top:4460px;"><li>Company</li><li>Platform</li><li>Solutions</li><li>Insights</li><li>Contact</li></ul>
<div class="abs" style="left:142px;top:4518px;width:916px;height:1px;background:rgba(255,255,255,.2);"></div>
<p class="abs" style="left:142px;top:4536px;font-size:12px;color:#fff;">© 2026 QP Fiduciary. All rights reserved. &nbsp;&nbsp;&nbsp;&nbsp;&nbsp;&nbsp; Privacy · Terms</p>
<div class="abs" role="img" aria-label="Social profile" style="left:1027px;top:4530px;width:30px;height:30px;border-radius:50%;background:#0094D4;"></div>

</div>
</body>
</html>
```